Verodex business card

Business card for sustainable investment company called "Verodex". Verodex is an exchange platform selling carbon credits between buyers and sellers. Carbon Credits are an environmental commodity for reducing global carbon emissions.

the card should obviously have our logo and the theme should be sustainability/environment mixed with a trading platform.

Contact Information for Business Card

Logo, Name, Title, Phone, Email

Colors
0054AA
0677BA
7BADD7
CADEEF
E8F1F8
0094D4
00A9DD
6FCCEA
C7EBF8
E9F6FB
00AB8E
00BBA5
67D7C9
C6EFE9
E9F9F6
59FF00
82FF00
B8FF75
E3FFCB
F4FFEA

```html
<!DOCTYPE html>
<html lang="en">
<head>
<meta charset="UTF-8">
<title>Verodex Business Card</title>
<link rel="stylesheet" href="https://fonts.googleapis.com/css2?family=Raleway:wght@400;700&display=swap">
<style>
  :root {
    --page-bg: #e6e2de;
    --teal: #1aa6ae;
    --cyan-glow: #5fd3e6;
    --ocean: #1b86c2;
    --royal: #2f62dc;
    --deep: #24488f;
    --panel-light: #c6e6ec;
    --panel-mid: #8fc3d6;
    --panel-edge: #e9eef2;
    --ink-light: #ece6da;
    --ink-soft: #e2ecf4;
    --ink-dark: #1c2a44;
    --brand-square: #0677BA;
  }
  * { margin: 0; padding: 0; box-sizing: border-box; }
  html, body {
    width: 1200px; height: 734px; overflow: hidden;
    background: var(--page-bg);
    font-family: "Raleway", sans-serif;
  }
  .card {
    position: absolute; left: 50px; top: 52px;
    width: 1100px; height: 630px;
    border-radius: 26px; overflow: hidden;
    background:
      radial-gradient(circle at 4% 18%, var(--cyan-glow) 0%, rgba(95,211,230,0) 32%),
      radial-gradient(circle at 30% 85%, #5a8ee6 0%, rgba(90,142,230,0) 40%),
      linear-gradient(165deg, var(--teal) 0%, var(--ocean) 45%, var(--royal) 100%);
    box-shadow: 0 10px 30px rgba(0,0,0,0.12);
  }
  .card__shade {
    position: absolute; left: 0; bottom: 0; width: 200px; height: 260px;
    background: linear-gradient(20deg, rgba(36,72,143,0.7), rgba(36,72,143,0));
  }
  .card__panel { position: absolute; inset: 0; }
  .identity { position: absolute; left: 78px; top: 196px; color: var(--ink-light); }
  .identity__name { font-weight: 700; font-size: 52px; letter-spacing: 0.5px; line-height: 1; }
  .identity__title { font-weight: 400; font-size: 30px; margin-top: 12px; color: var(--ink-soft); }
  .contact { position: absolute; left: 80px; top: 314px; list-style: none; color: var(--ink-soft); }
  .contact__item { display: flex; align-items: center; height: 39px; font-size: 29px; }
  .contact__icon { width: 26px; height: 26px; margin-right: 16px; fill: none; stroke: var(--ink-soft); stroke-width: 1.8; }
  .brand {
    position: absolute; left: 610px; top: 282px;
    display: flex; align-items: center;
  }
  .brand__square { width: 58px; height: 58px; background: var(--brand-square); margin-right: 22px; }
  .brand__name { font-weight: 700; font-size: 60px; color: var(--ink-dark); letter-spacing: 1px; line-height: 1; }
</style>
</head>
<body>
  <div class="card">
    <div class="card__shade"></div>
    <svg class="card__panel" viewBox="0 0 1100 630" aria-hidden="true">
      <defs>
        <linearGradient id="panelFill" x1="0" y1="0" x2="1" y2="1">
          <stop offset="0" stop-color="var(--panel-mid)"/>
          <stop offset="0.5" stop-color="var(--panel-light)"/>
          <stop offset="1" stop-color="var(--panel-mid)"/>
        </linearGradient>
      </defs>
      <polygon points="640,0 1100,0 1100,630 560,630" fill="var(--panel-edge)"/>
      <polygon points="660,0 1100,0 1100,630 580,630" fill="url(#panelFill)"/>
    </svg>

    <div class="identity">
      <h1 class="identity__name">MARCUS HALE</h1>
      <p class="identity__title">Founder &amp; CEO</p>
    </div>

    <ul class="contact">
      <li class="contact__item">
        <svg class="contact__icon" viewBox="0 0 24 24"><path d="M5 3h4l2 5-2.5 1.5a11 11 0 0 0 6 6L16 13l5 2v4a2 2 0 0 1-2 2A17 17 0 0 1 3 5a2 2 0 0 1 2-2z"/></svg>
        (555) 214-3098
      </li>
      <li class="contact__item">
        <svg class="contact__icon" viewBox="0 0 24 24"><rect x="2" y="5" width="20" height="14"/><path d="M2 5l10 8 10-8"/></svg>
        office@verodex.com
      </li>
      <li class="contact__item">
        <svg class="contact__icon" viewBox="0 0 24 24"><circle cx="12" cy="12" r="10"/><path d="M2 12h20M12 2c3 3 3 17 0 20M12 2c-3 3-3 17 0 20"/></svg>
        verodex.com
      </li>
    </ul>

    <div class="brand">
      <span class="brand__square"></span>
      <span class="brand__name">VERODEX</span>
    </div>
  </div>
</body>
</html>
```